New Business Card Design

We would like to refresh our business cards and make them look better. We are an IT company specialising in Cloud Services, IT Managed Services, software and hardware. I have attached a PSD of our current design. Also attached our logo.
Updates

I have uploaded all new logos in EPS format.

Can you please edit all designs to include a job title for Marcus Hollis, eg. General Manager

Industry/Entity Type

Software

Colors
ffffff

Requirements
Must have
• Please use white background.
Should not have
• Black background

```html
<!DOCTYPE html>
<html lang="en">
<head>
<meta charset="utf-8">
<title>Meridian Systems – Business Card</title>
<link rel="stylesheet" href="https://fonts.googleapis.com/css2?family=Open+Sans:wght@300;400;600&display=swap">
<style>
  :root {
    --page: #e9e9ec;
    --card: #ffffff;
    --red: #c0392b;
    --grey: #8a9399;
    --ink: #2b2f33;
    --muted: #5d6266;
    --faint-red: #f6e3e1;
  }
  * { box-sizing: border-box; margin: 0; padding: 0; }
  html, body { width: 1200px; height: 987px; overflow: hidden; }
  body {
    background: var(--page);
    font-family: "Open Sans", Arial, sans-serif;
    position: relative;
  }
  .card {
    position: absolute;
    left: 280px;
    width: 640px;
    height: 390px;
    background: var(--card);
    border-radius: 28px;
    overflow: hidden;
    box-shadow: 0 6px 18px rgba(0,0,0,.12);
  }
  .card--back { top: 70px; }
  .card--front { top: 527px; }

  /* Back */
  .back-mark {
    position: absolute;
    left: 300px; top: 40px;
    width: 220px; height: 220px;
    border-radius: 50%;
    background: var(--faint-red);
  }
  .back-brand {
    position: absolute;
    left: 0; right: 0; top: 110px;
    text-align: center;
    font-weight: 300;
    font-size: 58px;
    letter-spacing: 4px;
    color: var(--ink);
  }
  .back-tagline {
    position: absolute;
    left: 60px; right: 60px; top: 225px;
    text-align: center;
    font-size: 21px;
    line-height: 1.4;
    color: var(--muted);
  }

  /* Front */
  .name-tab {
    position: absolute;
    left: 0; top: 28px;
    width: 12px; height: 34px;
    background: var(--red);
  }
  .person { position: absolute; left: 42px; top: 28px; }
  .person__name { color: var(--red); font-weight: 600; font-size: 22px; line-height: 1.15; }
  .person__title { color: var(--ink); font-size: 15px; }
  .contacts {
    position: absolute; left: 42px; top: 120px;
    list-style: none;
  }
  .contacts li {
    display: flex; align-items: center; gap: 10px;
    font-size: 16px; color: var(--ink);
    height: 30px;
  }
  .contacts svg { width: 16px; height: 16px; fill: var(--red); }
  .bands { position: absolute; left: 0; top: 0; width: 640px; height: 390px; }
  .website {
    position: absolute; left: 42px; top: 268px;
    font-size: 17px; letter-spacing: 1.5px; color: #ffffff;
  }
  .brand {
    position: absolute; right: 40px; top: 150px;
    display: flex; align-items: center; gap: 16px;
  }
  .brand__dot {
    width: 64px; height: 64px; border-radius: 50%;
    background: var(--red);
  }
  .brand__name {
    font-weight: 300; font-size: 40px; letter-spacing: 3px;
    color: var(--ink); line-height: 1.05;
  }
</style>
</head>
<body>

<section class="card card--back" aria-label="Card back">
  <div class="back-mark" aria-hidden="true"></div>
  <div class="back-brand">Meridian Systems</div>
  <p class="back-tagline">We are an IT company specializing in Cloud Services IT Managed Services, software and hardware</p>
</section>

<section class="card card--front" aria-label="Card front">
  <div class="name-tab"></div>
  <div class="person">
    <p class="person__name">Marcus Hollis</p>
    <p class="person__title">General Manager</p>
  </div>

  <ul class="contacts">
    <li>
      <svg viewBox="0 0 16 16" aria-hidden="true"><path d="M3.5 1.5l2.5 0 1 3.5-1.6 1.2a8 8 0 0 0 4.4 4.4L11 9l3.5 1v2.5c0 1-1 2-2 2C6.5 14.5 1.5 9.5 1.5 3.5c0-1 1-2 2-2z"/></svg>
      07 5550 1840
    </li>
    <li>
      <svg viewBox="0 0 16 16" aria-hidden="true"><path d="M4.5 0.5h7a1 1 0 0 1 1 1v13a1 1 0 0 1-1 1h-7a1 1 0 0 1-1-1v-13a1 1 0 0 1 1-1zM5 3v8h6V3zM8 12.2a0.9 0.9 0 1 0 0 1.8a0.9 0.9 0 1 0 0-1.8z"/></svg>
      0400 555 017
    </li>
    <li>
      <svg viewBox="0 0 16 16" aria-hidden="true"><path d="M1 3.5h14v9H1zM2 4.5l6 4.5 6-4.5v-0.2H2z" fill-rule="evenodd"/></svg>
      hollism@meridiansys.com.au
    </li>
  </ul>

  <svg class="bands" viewBox="0 0 640 390" aria-hidden="true">
    <path d="M0 258 H250 C285 258 290 312 330 312 H640 V390 H0 Z" fill="#8a9399"/>
    <path d="M0 302 H240 C272 302 280 330 315 330 H640 V390 H0 Z" fill="#c0392b"/>
  </svg>
  <p class="website">www.meridiansys.com.au</p>

  <div class="brand">
    <div class="brand__dot" aria-hidden="true"></div>
    <div class="brand__name">Meridian<br>Systems</div>
  </div>
</section>

</body>
</html>
```